Build a landing page to promote a service (dialler consultation and support).

We are a call centre consultation firm and we need a landing page to promote a service. The service is Tormalux dialler consultation and support.
If you do not know what Tormalux is, please do some quick "Zorvex" research for more information.
The landing page will be promoted with a paid advertisement, so we want something that is simple, and explains exactly what service we offer.
There are two objectives for the landing page:
1) A "call to action" which directs the user to a contact page, including a form plus all of our contact details.
2) A form for them viewers to enter their details to get a "FREE" quote for their project. This form should be placed on the main page.
Notes:
The call to action will require the viewer to enter their name, email, phone number as well as a description of their request. There will also need to be a drop down menu for the type of quote. This menu should have the following options:
1) Tormalux support
2) Tormalux hosting
3) Tormalux customisation
4) Other
We need 2 pages in total:
1) Main landing page
This is the home page. It will need to clearly indicate our services and our key selling features.
Services:
* Tormalux support
* Tormalux hosting
* Tormalux customisation
Key Selling Features:
* Australian based
* PCI complaint
* 10+ years of dialler and call centre experience
* we run a sister company which is a highly reputable 40 seat call centre, so we know first hand about call centre technology.
The main landing page will have an "about us" section with a few paragraphs about how we got started.
-------------------------------------------------------------------------
2) Contact page
All of our contact details will live on this page, as well as a contact form.
Other notes:
We will be self hosting the landing page.
We already have a domain name.
The design must be clean and incorporate our logo, as well as it's colours. (Logo attached)
We want a fully function HTML landing page, not just a "PSD" design.
The page must be mobile optimised.
Anyone using Tormalux software.

```html
<!DOCTYPE html>
<html lang="en">
<head>
<meta charset="utf-8">
<title>Ridgewave – Call Centre Consultation</title>
<link href="https://fonts.googleapis.com/css2?family=Montserrat:wght@400;600;700&family=Open+Sans:wght@400;600&display=swap" rel="stylesheet">
<style>
:root{
  --teal:#2aa98b;
  --blue:#1b7dc3;
  --blue-dark:#14649f;
  --ink:#1f1f1f;
  --muted:#6f6f6f;
  --sheet:#d9d9d9;
  --light:#f3f1f4;
  --grey:#a4a3a2;
  --white:#ffffff;
}
*{margin:0;padding:0;box-sizing:border-box}
html,body{width:1200px;height:3830px;overflow:hidden}
body{background:var(--sheet);font-family:"Open Sans",Arial,sans-serif;color:var(--ink);position:relative}
.page{position:absolute;left:77px;width:1057px;background:var(--white);overflow:hidden}
.page--home{top:38px;height:2354px}
.page--contact{top:2438px;height:1353px}
.abs{position:absolute}
.h-font{font-family:"Montserrat",Arial,sans-serif}

/* nav */
.nav{position:absolute;left:0;top:0;width:100%;height:72px;background:var(--white);z-index:3}
.nav__item{position:absolute;top:27px;font:600 11px "Montserrat",Arial,sans-serif;color:var(--ink);padding:4px 7px;text-transform:uppercase}
.nav__item--active{background:var(--teal);color:var(--white)}
.nav__search{position:absolute;left:1000px;top:23px;width:24px;height:24px;border-radius:50%;background:var(--blue)}
.brand{position:absolute;left:107px;top:-74px;width:210px;height:210px;border-radius:50%;background:var(--white);z-index:4}
.brand__dot{position:absolute;left:83px;top:92px;width:44px;height:44px;border-radius:50%;background:var(--blue)}
.brand__name{position:absolute;left:0;width:210px;top:142px;text-align:center;font:600 28px "Montserrat",Arial,sans-serif;color:var(--blue)}

/* hero */
.hero{position:absolute;left:0;top:72px;width:100%;height:554px;background:linear-gradient(100deg,#5b4a42 0%,#8a7a70 35%,#d9c9bd 62%,#b69e8f 82%,#6f5f56 100%)}
.arrow{position:absolute;width:22px;height:22px;border-left:3px solid var(--white);border-bottom:3px solid var(--white)}
.arrow--prev{transform:rotate(45deg)}
.arrow--next{transform:rotate(-135deg)}
.quote{position:absolute;left:120px;top:112px;width:271px;height:383px;background:rgba(18,18,18,.88);padding:20px 22px}
.quote__title{font:700 21px "Montserrat",Arial,sans-serif;color:var(--white);line-height:1.1}
.quote__sub{font:400 21px "Montserrat",Arial,sans-serif;color:var(--white);letter-spacing:.5px;margin-bottom:20px}
.field{display:block;width:100%;height:30px;border:1.5px solid var(--white);background:transparent;color:var(--white);font-size:10px;padding:7px 8px;margin-bottom:10px}
.field--area{height:66px}
.field--select{position:relative}
.field--select::after{content:"";position:absolute;right:8px;top:11px;border:4px solid transparent;border-top-color:var(--white)}
.quote__btn{display:block;width:100%;height:32px;background:var(--teal);color:var(--white);text-align:center;font:700 13px/32px "Montserrat",Arial,sans-serif;margin-top:6px}

/* sections */
.section-title{position:absolute;left:0;width:100%;text-align:center;font:700 23px "Montserrat",Arial,sans-serif}
.section-rule{position:absolute;left:512px;width:33px;height:2px;background:#9a9a9a}
.services{position:absolute;left:0;top:626px;width:100%;height:516px;background:var(--light)}
.badge{position:absolute;border-radius:50%;background:var(--blue);box-shadow:0 0 0 4px var(--white),0 0 0 6px var(--teal)}
.badge svg{position:absolute;left:50%;top:50%;transform:translate(-50%,-50%)}
.service{position:absolute;width:220px;text-align:center}
.service__name{font:700 15px "Montserrat",Arial,sans-serif;margin-bottom:14px}
.service__text{font-size:10px;line-height:1.5;color:var(--muted)}
.btn-small{position:absolute;background:var(--teal);color:var(--white);font:700 10px/22px "Montserrat",Arial,sans-serif;padding:0 12px;height:22px}

.features{position:absolute;left:0;top:1142px;width:100%;height:421px;background:var(--white)}
.feature{position:absolute;width:200px;text-align:center;font-size:11.5px;line-height:1.45;color:var(--ink)}
.divider{position:absolute;top:210px;width:1px;height:205px;background:#e3e3e3}

.about{position:absolute;left:0;top:1563px;width:100%;height:462px;background:var(--grey)}
.about__title{position:absolute;left:166px;top:98px;font:700 25px "Montserrat",Arial,sans-serif;color:var(--white)}
.about__rule{position:absolute;left:166px;top:134px;width:33px;height:2px;background:var(--white)}
.about__lead{position:absolute;left:166px;top:156px;width:340px;font:700 12.5px/1.45 "Open Sans",Arial,sans-serif;color:var(--white)}
.about__text{position:absolute;left:166px;top:215px;width:340px;font-size:12px;line-height:1.5;color:#ececec}
.about__photo{position:absolute;left:561px;top:33px;width:345px;height:429px;background:linear-gradient(180deg,#8d8b89 0%,#c9c5c2 40%,#efefef 75%,#dedede 100%);border-radius:150px 150px 0 0}

/* footer */
.footer{position:absolute;left:0;width:100%;height:329px;background:linear-gradient(110deg,var(--blue) 0%,#2a8fd4 45%,var(--blue) 70%,var(--blue-dark) 100%);color:var(--white)}
.footer__dot{position:absolute;left:203px;top:56px;width:58px;height:58px;border-radius:50%;border:4px solid var(--white)}
.footer__name{position:absolute;left:105px;top:124px;width:255px;text-align:center;font:600 37px "Montserrat",Arial,sans-serif}
.footer__head{position:absolute;top:60px;font:700 10px "Montserrat",Arial,sans-serif;text-transform:uppercase}
.footer__list{position:absolute;top:82px;list-style:none;font-size:10px;line-height:1.55}
.footer__row{display:flex;gap:9px;margin-bottom:10px}
.footer__row svg{flex:none;margin-top:2px}
.social{display:flex;align-items:center;gap:10px;margin-bottom:10px}
.social i{display:block;width:22px;height:22px;border-radius:50%;background:var(--blue-dark)}
.footer__line{position:absolute;left:418px;top:222px;width:560px;height:1px;background:rgba(255,255,255,.3)}
.footer__copy{position:absolute;left:0;width:100%;top:252px;text-align:center;font-size:9.5px}

/* contact page */
.map{position:absolute;left:0;top:72px;width:100%;height:472px;background:linear-gradient(160deg,#c9c9c9 0%,#d8d8d6 45%,#c4c4c2 100%)}
.contact{position:absolute;left:0;top:544px;width:100%;height:483px;background:var(--white)}
.info{position:absolute;left:153px;display:flex;gap:16px;align-items:flex-start}
.info__icon{flex:none;width:30px;height:30px;border-radius:50%;background:var(--teal);display:flex;align-items:center;justify-content:center}
.info__label{font-size:10px;color:var(--ink)}
.info__main{font-size:13.5px;line-height:1.4}
.info__small{font-size:9.5px;color:var(--muted)}
.touch__title{position:absolute;left:495px;top:83px;font:400 28px "Open Sans",Arial,sans-serif;color:#333}
.input{position:absolute;height:36px;border:1px solid #dadada;font-size:10px;color:#555;padding:11px 10px;background:var(--white)}
.submit{position:absolute;left:495px;top:385px;width:92px;height:32px;background:var(--teal);color:var(--white);font:600 14px/32px "Open Sans",Arial,sans-serif;text-align:center}
</style>
</head>
<body>

<!-- Home page -->
<section class="page page--home">
  <div class="brand"><span class="brand__dot"></span><span class="brand__name">Ridgewave</span></div>
  <nav class="nav">
    <span class="nav__item nav__item--active" style="left:557px">Home</span>
    <span class="nav__item" style="left:626px">About us</span>
    <span class="nav__item" style="left:718px">Services</span>
    <span class="nav__item" style="left:808px">Contact us</span>
    <span class="nav__search"></span>
  </nav>

  <div class="hero" role="img" aria-label="Photo of a smiling call centre agent wearing a headset">
    <span class="arrow arrow--prev" style="left:46px;top:266px"></span>
    <span class="arrow arrow--next" style="left:990px;top:266px"></span>
    <form class="quote">
      <div class="quote__title">CALL CENTRE</div>
      <div class="quote__sub">CONSULTATION</div>
      <span class="field">Name</span>
      <span class="field">E mail id</span>
      <span class="field">Ph No.</span>
      <span class="field field--select">Type of quote</span>
      <span class="field field--area">Message</span>
      <span class="quote__btn">GET A QUOTE</span>
    </form>
  </div>

  <section class="services">
    <h2 class="section-title" style="top:58px">OUR SERVICES</h2>
    <span class="section-rule" style="top:97px"></span>

    <span class="badge" style="left:179px;top:161px;width:97px;height:97px">
      <svg width="48" height="48" viewBox="0 0 48 48" fill="none" stroke="#fff" stroke-width="3"><path d="M8 30v-6a16 16 0 0 1 32 0v6"/><rect x="6" y="28" width="8" height="12" rx="2" fill="#fff"/><rect x="34" y="28" width="8" height="12" rx="2" fill="#fff"/></svg>
    </span>
    <span class="badge" style="left:483px;top:161px;width:97px;height:97px">
      <svg width="44" height="44" viewBox="0 0 44 44" fill="none" stroke="#fff" stroke-width="3"><rect x="6" y="5" width="32" height="10" rx="2"/><rect x="6" y="17" width="32" height="10" rx="2"/><rect x="6" y="29" width="32" height="10" rx="2"/><path d="M11 10h10M11 22h10M11 34h10"/></svg>
    </span>
    <span class="badge" style="left:766px;top:161px;width:97px;height:97px">
      <svg width="46" height="46" viewBox="0 0 46 46" fill="none" stroke="#fff" stroke-width="3"><circle cx="18" cy="26" r="9"/><circle cx="18" cy="26" r="3"/><path d="M18 12v4M18 36v4M4 26h4M28 26h4M8 16l3 3M25 33l3 3M8 36l3-3M25 19l3-3"/><circle cx="34" cy="12" r="5"/><path d="M34 3v3M34 18v3M25 12h3M40 12h3"/></svg>
    </span>

    <div class="service" style="left:117px;top:306px">
      <h3 class="service__name">Tormalux Support</h3>
      <p class="service__text">At vero eos et accusamus et iusto odio dignissimos ducimus qui blanditiis praesentium voluptatum deleniti atque corrupti quos dolores et quas molestias excepturi sint occaecati.</p>
    </div>
    <div class="service" style="left:421px;top:306px">
      <h3 class="service__name">Tormalux Hosting</h3>
      <p class="service__text">At vero eos et accusamus et iusto odio dignissimos ducimus qui blanditiis praesentium voluptatum deleniti atque corrupti quos dolores et quas molestias excepturi sint occaecati.</p>
    </div>
    <div class="service" style="left:704px;top:306px">
      <h3 class="service__name">Tormalux Customisation</h3>
      <p class="service__text">At vero eos et accusamus et iusto odio dignissimos ducimus qui blanditiis praesentium voluptatum deleniti atque corrupti quos dolores et quas molestias excepturi sint occaecati.</p>
    </div>

    <span class="btn-small" style="left:186px;top:433px">READ MORE</span>
    <span class="btn-small" style="left:490px;top:433px">READ MORE</span>
    <span class="btn-small" style="left:773px;top:433px">READ MORE</span>
  </section>

  <section class="features">
    <h2 class="section-title" style="top:60px">FEATURES</h2>
    <span class="section-rule" style="top:99px"></span>

    <span class="badge" style="left:134px;top:187px;width:90px;height:90px">
      <svg width="40" height="40" viewBox="0 0 40 40" fill="none" stroke="#fff" stroke-width="3"><path d="M20 36s-11-11-11-20a11 11 0 0 1 22 0c0 9-11 20-11 20z"/><circle cx="20" cy="16" r="4" fill="#fff"/></svg>
    </span>
    <span class="badge" style="left:312px;top:187px;width:90px;height:90px">
      <svg width="40" height="40" viewBox="0 0 40 40" fill="none" stroke="#fff" stroke-width="3"><rect x="6" y="8" width="24" height="26" rx="2"/><path d="M16 24l2-6 14-14 4 4-14 14z"/></svg>
    </span>
    <span class="badge" style="left:519px;top:187px;width:90px;height:90px">
      <svg width="42" height="42" viewBox="0 0 42 42" fill="#fff"><path d="M15 8h12v5h-3v-2h-6v2h-3z"/><rect x="5" y="13" width="32" height="22" rx="3"/></svg>
    </span>
    <span class="badge" style="left:774px;top:187px;width:90px;height:90px">
      <svg width="44" height="44" viewBox="0 0 44 44" fill="#fff"><rect x="6" y="22" width="32" height="4"/><rect x="8" y="26" width="3" height="12"/><rect x="33" y="26" width="3" height="12"/><rect x="18" y="10" width="14" height="10" rx="1"/><circle cx="11" cy="16" r="4"/></svg>
    </span>

    <span class="divider" style="left:268px"></span>
    <span class="divider" style="left:455px"></span>
    <span class="divider" style="left:679px"></span>

    <p class="feature" style="left:79px;top:310px">Australian based</p>
    <p class="feature" style="left:257px;top:310px">PCI complaint</p>
    <p class="feature" style="left:464px;top:310px">10+ years of dialler and<br>call centre experience</p>
    <p class="feature" style="left:719px;top:310px">we run a sister company which is a highly reputable 40 seat call centre, so we know first hand about call centre technology.</p>
  </section>

  <section class="about">
    <h2 class="about__title">ABOUT US</h2>
    <span class="about__rule"></span>
    <p class="about__lead">Lorem Ipsum is simply dummy text of the printing and typesetting industry</p>
    <p class="about__text">At vero eos et accusamus et iusto odio dignissimos ducimus qui blanditiis praesentium voluptatum deleniti atque corrupti quos dolores et quas molestias excepturi sint occaecati. passage of Lorem Ipsum, you need to be sure there isn't anything embarrassing hidden in the middle of text.</p>
    <span class="btn-small" style="left:166px;top:362px;height:28px;line-height:28px;font-size:11px">READ MORE</span>
    <div class="about__photo" role="img" aria-label="Photo of a consultant in shirt and tie wearing a headset, pointing to the text"></div>
  </section>

  <footer class="footer" style="top:2025px">
    <span class="footer__dot"></span>
    <span class="footer__name">Ridgewave</span>

    <h4 class="footer__head" style="left:419px">Contact us</h4>
    <ul class="footer__list" style="left:419px">
      <li class="footer__row"><svg width="10" height="12" viewBox="0 0 10 12" fill="#fff"><path d="M5 12S0 7 0 4.5a5 5 0 0 1 10 0C10 7 5 12 5 12z"/></svg><span>418 Harbour Lane,<br>Kelton, NS 2410</span></li>
      <li class="footer__row"><svg width="10" height="10" viewBox="0 0 10 10" fill="#fff"><path d="M2 0l2 2.5-1 1.5a6 6 0 0 0 3 3l1.5-1L10 8l-2 2C4 10 0 6 0 2z"/></svg><span>555-010-4420</span></li>
      <li class="footer__row"><svg width="11" height="8" viewBox="0 0 11 8" fill="#fff"><rect width="11" height="8" rx="1"/></svg><span>info@ridgewave.example</span></li>
    </ul>

    <h4 class="footer__head" style="left:646px">Menu</h4>
    <ul class="footer__list" style="left:646px;line-height:1.5">
      <li>Home</li><li>About Us</li><li>Services</li><li>Contact Us</li>
    </ul>

    <h4 class="footer__head" style="left:824px">Connect with us</h4>
    <ul class="footer__list" style="left:824px;top:80px;list-style:none">
      <li class="social"><i></i>Chatter</li>
      <li class="social"><i></i>Postline</li>
      <li class="social"><i></i>Linkhub</li>
    </ul>

    <span class="footer__line"></span>
    <p class="footer__copy">Copyrights © 2016 All Rights Reserved</p>
  </footer>
</section>

<!-- Contact page -->
<section class="page page--contact">
  <div class="brand"><span class="brand__dot"></span><span class="brand__name">Ridgewave</span></div>
  <nav class="nav">
    <span class="nav__item" style="left:567px">Home</span>
    <span class="nav__item" style="left:631px">About us</span>
    <span class="nav__item" style="left:718px">Services</span>
    <span class="nav__item nav__item--active" style="left:802px">Contact us</span>
    <span class="nav__search"></span>
  </nav>

  <div class="map" role="img" aria-label="Street map showing the office location marked with a pin">
    <span class="arrow arrow--prev" style="left:46px;top:225px"></span>
    <span class="arrow arrow--next" style="left:990px;top:225px"></span>
  </div>

  <section class="contact">
    <div class="info" style="top:76px">
      <span class="info__icon"><svg width="10" height="13" viewBox="0 0 10 13" fill="#fff"><path d="M5 13S0 7.5 0 5a5 5 0 0 1 10 0c0 2.5-5 8-5 8z"/></svg></span>
      <p class="info__main">2716 Maple Crest Road<br>Brindale, VC 3021</p>
    </div>
    <div class="info" style="top:160px">
      <span class="info__icon"><svg width="12" height="12" viewBox="0 0 10 10" fill="#fff"><path d="M2 0l2 2.5-1 1.5a6 6 0 0 0 3 3l1.5-1L10 8l-2 2C4 10 0 6 0 2z"/></svg></span>
      <div><p class="info__label">CALL US:</p><p class="info__main" style="text-decoration:underline">555.010.4420</p><p class="info__small">Monday-Friday 9am-6pm</p></div>
    </div>
    <div class="info" style="top:248px">
      <span class="info__icon"><svg width="13" height="9" viewBox="0 0 13 9" fill="none" stroke="#fff" stroke-width="1.5"><rect x=".75" y=".75" width="11.5" height="7.5"/><path d="M1 1l5.5 4L12 1"/></svg></span>
      <div><p class="info__label">E MAIL US:</p><p class="info__main">info@ridgewave.example</p></div>
    </div>
    <div class="info" style="top:330px">
      <span class="info__icon"><svg width="13" height="13" viewBox="0 0 13 13" fill="none" stroke="#fff" stroke-width="1.5"><circle cx="6.5" cy="6.5" r="5.5"/><path d="M6.5 3v3.5l2.5 1.5"/></svg></span>
      <div><p class="info__label">Our office is open</p><p class="info__main">Mon to Fri from 8am to 6pm</p></div>
    </div>

    <h2 class="touch__title">Get in Touch</h2>
    <span class="input" style="left:495px;top:139px;width:207px">Name *</span>
    <span class="input" style="left:715px;top:139px;width:204px">E mail *</span>
    <span class="input" style="left:495px;top:190px;width:207px">Company</span>
    <span class="input" style="left:715px;top:190px;width:204px">Phone</span>
    <span class="input" style="left:495px;top:225px;width:424px;height:117px">Message</span>
    <span class="submit">Submit</span>
  </section>

  <footer class="footer" style="top:1027px;height:326px">
    <span class="footer__dot"></span>
    <span class="footer__name">Ridgewave</span>

    <h4 class="footer__head" style="left:425px">Contact us</h4>
    <ul class="footer__list" style="left:425px">
      <li class="footer__row"><svg width="10" height="12" viewBox="0 0 10 12" fill="#fff"><path d="M5 12S0 7 0 4.5a5 5 0 0 1 10 0C10 7 5 12 5 12z"/></svg><span>418 Harbour Lane,<br>Kelton, NS 2410</span></li>
      <li class="footer__row"><svg width="10" height="10" viewBox="0 0 10 10" fill="#fff"><path d="M2 0l2 2.5-1 1.5a6 6 0 0 0 3 3l1.5-1L10 8l-2 2C4 10 0 6 0 2z"/></svg><span>555-010-4420</span></li>
      <li class="footer__row"><svg width="11" height="8" viewBox="0 0 11 8" fill="#fff"><rect width="11" height="8" rx="1"/></svg><span>info@ridgewave.example</span></li>
    </ul>

    <h4 class="footer__head" style="left:652px">Menu</h4>
    <ul class="footer__list" style="left:652px;line-height:1.5">
      <li>Home</li><li>About Us</li><li>Services</li><li>Contact Us</li>
    </ul>

    <h4 class="footer__head" style="left:830px">Connect with us</h4>
    <ul class="footer__list" style="left:830px;top:80px">
      <li class="social"><i></i>Chatter</li>
      <li class="social"><i></i>Postline</li>
      <li class="social"><i></i>Linkhub</li>
    </ul>

    <span class="footer__line"></span>
    <p class="footer__copy">Copyrights © 2016 All Rights Reserved</p>
  </footer>
</section>

</body>
</html>
```